Software Company Banner Ad

We need a banner ad in two sizes. 728x90 and 300x250.
They should have strong similarity to the following ads:
http://www.quellara.com/search/results?brand[0]=zorvik&ad=4812096
http://www.quellara.com/search/results?brand[0]=tralvenco&ad=4826173
Idea will be very similar. We want the same grey color, white text, and a realistic owl that blinks. The owl should have dramatic, bright, yellow eyes. The text will animate "from the top" as in the example. Though the logo animation will be different, all text and non-logo animation should match the animation in the example advertisements. The text will rotate between the following four sentences and images.
Looking for a provider of procurement cloud apps?
[Images - attached below]
The experts really liked our PLW booth.
Get great results with every procurement. [Learn more]
There are three vector files attached below. Feel free to change the colors as necessary to match the color scheme of the ad. We need one 2013 and one 2014 award in the ad.
The awards could appear simultaneously, could swap with each other or could appear in succession. Animation is acceptable.
There is an additional vector file with the company logo. The company logo should go where the Zorvik logo is in horizontal ad. The company logo should go where the Tralvenco logo is in the block ad. The example ad has two logos. We will only need one logo on our ads. The logo should be changed to the color of the text used for the ad (white).
The owls eyes should slowly blink two times (as in the example).
The owl eyes should immediately grab someone's attention and all colors should compliment these eyes.
The [Learn more] button should have animation. The button should match the color of the owl's eyes. There should be a line/gleam/glare of light that travels across the button. The button should be embossed with the subtle animation occurring each time it appears.
Ads should be done with flash. We will need the source files and the names of any fonts used at the end of the project.
Thank you and please do not hesitate to contact with any questions.
Updates
Project Deadline Extended
Reason: We have contacted several photographers to see if the alternative owl images are available on pixHarb, Framelodgery or similar. The duration extension is to accommodate this.
Target Market(s)
Target customers are procurement department employees of large companies.
Industry/Entity Type
It Company

```html
<!DOCTYPE html>
<html lang="en">
<head>
<meta charset="utf-8">
<title>Sample 2 (Block ad)</title>
<link rel="stylesheet" href="https://fonts.googleapis.com/css2?family=Source+Sans+3:wght@400;600;700&display=swap">
<style>
  :root {
    --ink: #333333;
    --band: #7f7f7f;
    --white: #ffffff;
    --bg-center: #ffffff;
    --bg-edge: #e2e2e2;
    --button: #f7b500;
    --button-ink: #1a1a1a;
    --photo-dark: #5a3b20;
    --photo-mid: #a07448;
    --photo-light: #c9ab86;
    --award-orange: #f08a1c;
  }
  * { margin: 0; padding: 0; box-sizing: border-box; }
  html, body { width: 1200px; height: 1000px; overflow: hidden; }
  body {
    font-family: "Source Sans 3", "Myriad Pro", Arial, sans-serif;
    color: var(--ink);
    background: radial-gradient(ellipse at 50% 40%, var(--bg-center) 0%, #f4f4f4 45%, var(--bg-edge) 100%);
    position: relative;
  }
  .sheet-title {
    position: absolute; top: 44px; left: 0; width: 1200px;
    text-align: center; font-size: 40px; font-weight: 700; letter-spacing: -0.3px;
  }
  .slide-heading {
    position: absolute; font-size: 32px; font-weight: 400; white-space: nowrap; line-height: 1;
  }
  .slide-heading small { font-size: 16px; margin-left: 4px; }
  .slide-heading.stacked { text-align: center; width: 360px; }
  .slide-heading.stacked small { display: block; margin: 6px 0 0; }
  .ad {
    position: absolute; width: 300px; height: 250px; overflow: hidden;
  }
  .ad-photo {
    height: 168px;
    background:
      radial-gradient(ellipse 60% 70% at 50% 55%, var(--photo-light) 0%, var(--photo-mid) 45%, transparent 80%),
      linear-gradient(180deg, var(--photo-dark), var(--photo-mid) 60%, #d9cfc2 100%);
  }
  .ad-band {
    position: relative; height: 82px; background: var(--band); color: var(--white);
  }
  .ad-copy {
    position: absolute; font-size: 19px; line-height: 24px;
  }
  .award-badge {
    position: absolute; left: 17px; top: 12px; width: 56px; height: 56px;
    background: var(--white); border-bottom: 14px solid var(--award-orange);
  }
  .award-source { position: absolute; left: 109px; top: 20px; font-size: 16px; line-height: 1; }
  .award-title { position: absolute; left: 109px; top: 40px; font-size: 18px; font-weight: 700; line-height: 1; }
  .cta-copy { position: absolute; left: 47px; top: 6px; font-size: 16px; line-height: 20px; }
  .learn-more {
    position: absolute; left: 8px; top: 51px; width: 81px; height: 24px;
    background: linear-gradient(180deg, #ffd24a, var(--button));
    border-radius: 3px; color: var(--button-ink);
    font-family: Arial, sans-serif; font-size: 12px; line-height: 24px; text-align: center;
  }
  .brand-name {
    position: absolute; right: 11px; top: 56px; font-size: 17px; font-weight: 700; letter-spacing: 1px; line-height: 1;
  }
</style>
</head>
<body>
  <h1 class="sheet-title">Sample 2 (Block ad)</h1>

  <div class="slide-heading" style="left:290px; top:132px;">Slide 1<small>with tagline</small></div>
  <section class="ad" style="left:231px; top:183px;">
    <div class="ad-photo" role="img" aria-label="Close-up photo of a horned owl with bright yellow eyes open"></div>
    <div class="ad-band"><p class="ad-copy" style="left:43px; top:15px;">Looking for a provider of<br>procurement cloud apps?</p></div>
  </section>

  <div class="slide-heading" style="left:767px; top:132px;">Slide 2<small>with tagline</small></div>
  <section class="ad" style="left:711px; top:183px;">
    <div class="ad-photo" role="img" aria-label="Close-up photo of a horned owl with bright yellow eyes open"></div>
    <div class="ad-band"><p class="ad-copy" style="left:39px; top:15px;">The experts really liked our<br>PLW booth</p></div>
  </section>

  <div class="slide-heading" style="left:266px; top:540px;">Slide 3<small>with award 2013</small></div>
  <section class="ad" style="left:232px; top:587px;">
    <div class="ad-photo" role="img" aria-label="Close-up photo of a horned owl with its eyes closed"></div>
    <div class="ad-band">
      <div class="award-badge" role="img" aria-label="Award badge"></div>
      <p class="award-source">Sourcing Digest</p>
      <p class="award-title">BEST OF SHOW 2013</p>
    </div>
  </section>

  <div class="slide-heading stacked" style="left:677px; top:519px;">Slide 4<small>with Learn more button and eyes close sample</small></div>
  <section class="ad" style="left:711px; top:587px;">
    <div class="ad-photo" role="img" aria-label="Close-up photo of a horned owl with bright yellow eyes open"></div>
    <div class="ad-band">
      <p class="cta-copy">Get great results with every<br>procurement</p>
      <div class="learn-more">Learn More</div>
      <p class="brand-name">VERANQ</p>
    </div>
  </section>
</body>
</html>
```